Broschüre für Anbieter von Haushaltshilfen und Alltagsbegleitern für Privathaushalte
Zielgruppe
Wir bieten Haushaltshilfen und Alltagsbegleiter für Privathaushalte an. Unsere Hauptkundenklientel sind Pflegebedürftige Menschen denen eine Haushaltshilfe von der Pflegekasse zusteht. Weitere Kunden sind Familien und/oder Singlehaushalte, die eine Haushaltfshilfe benötigen.
Aufgabenstellung
- Das Prospekt sollte DIN A4 sein, sind aber auch offen für andere Formate
- Farbdesign muß unsere Logofarben enthalten
- In dem Prospekt müßen unsere Leistungen wie auf unserer Internetseite www.wolkenmut.de beschrieben sein.
- Seitenanzahl insgesamt 4 Seiten

```html
<!DOCTYPE html>
<html lang="de">
<head>
<meta charset="utf-8">
<title>Wolkenmut – Broschüre Innenseiten</title>
<link href="https://fonts.googleapis.com/css2?family=Montserrat:wght@300;400;500;600;700;800&display=swap" rel="stylesheet">
<style>
  :root{
    --red:#c0161f;
    --dark:#3a3a3a;
    --grey:#8f8f8f;
    --text:#4a4a4a;
    --paper:#ffffff;
    --bg:#f1f1f1;
    --fold:#e6e6e6;
  }
  *{margin:0;padding:0;box-sizing:border-box}
  html,body{width:1200px;height:1200px;overflow:hidden;background:var(--bg);font-family:"Montserrat",sans-serif}
  .stage{position:relative;width:1200px;height:1200px}
  .spread{
    position:absolute;left:30px;top:197px;width:1476px;height:1044px;
    transform:scale(0.7724);transform-origin:0 0;
    background:var(--paper);overflow:hidden;
    box-shadow:0 10px 30px rgba(0,0,0,.12);
  }
  .fold{position:absolute;top:0;bottom:0;width:1px;background:var(--fold)}
  .fold--a{left:496px}.fold--b{left:991px}
  .deco{position:absolute;left:0;top:0}

  /* left panel */
  .intro-card{position:absolute;left:52px;top:52px;width:392px;height:939px;background:var(--dark);border-radius:22px;overflow:hidden;color:#fff}
  .intro-card svg{position:absolute;left:0;top:0}
  .intro-text{position:absolute;left:50px;top:224px;width:292px;font-weight:300;font-size:17.5px;line-height:28px;letter-spacing:-0.2px;text-align:justify;hyphens:manual}
  .intro-text p{margin-bottom:12px}
  .intro-text strong{font-weight:600}
  .audience{position:absolute;top:768px;width:150px;text-align:center;font-size:13px;font-weight:600;line-height:16px}
  .audience svg{position:static;display:block;margin:0 auto 8px}
  .audience--care{left:36px}.audience--family{left:206px}

  /* middle panel */
  .heading{position:absolute;left:549px;line-height:1}
  .heading .light{display:block;font-size:36px;font-weight:500;letter-spacing:1px}
  .heading .bold{display:block;font-size:40px;font-weight:800;letter-spacing:1px}
  .heading--why{top:60px}.heading--why .light{color:var(--dark)}.heading--why .bold{color:var(--red)}
  .heading--services{top:584px}.heading--services .light{color:var(--red)}.heading--services .bold{color:var(--dark)}
  .body{position:absolute;left:549px;width:392px;font-size:18px;font-weight:300;line-height:29px;letter-spacing:-0.2px;color:var(--text);text-align:justify;hyphens:manual}
  .body--why{top:150px}.body--services{top:684px}
  .body .brand{color:var(--red);font-weight:600}
  .benefits-frame{position:absolute;left:558px;top:400px;width:400px;height:168px;border:3px solid var(--dark);border-top:none;border-left:none;border-radius:0 0 8px 8px}
  .benefit{position:absolute;background:var(--grey);color:#fff;font-size:14px;line-height:17px;display:flex;align-items:center;justify-content:center;text-align:center;padding:0 4px}
  .b1{left:548px;top:374px;width:126px;height:108px;border-radius:6px 0 0 0}
  .b2{left:682px;top:374px;width:126px;height:108px}
  .b3{left:815px;top:374px;width:126px;height:108px;border-radius:0 6px 0 0}
  .b4{left:548px;top:486px;width:393px;height:68px;border-radius:0 0 6px 6px}

  .service{position:absolute;top:800px;width:140px;text-align:center;color:var(--red);font-size:17px;font-weight:600;line-height:18px}
  .service svg{display:block;margin:0 auto 30px}

  /* right panel */
  .photo{position:absolute;left:1024px;top:0;width:452px;height:616px;border-radius:0 0 0 30px;
    background:radial-gradient(circle at 45% 35%,#eeeeee 0%,#d8d4d0 35%,#8d8bb8 62%,#b9a58a 85%,#d9cfc4 100%)}
</style>
</head>
<body>
<div class="stage">
  <div class="spread">
    <svg class="deco" width="1476" height="1044" viewBox="0 0 1476 1044" aria-hidden="true">
      <circle cx="1071" cy="-136" r="210" fill="var(--dark)"/>
      <circle cx="1000" cy="-230" r="314" fill="none" stroke="var(--red)" stroke-width="3"/>
      <circle cx="1440" cy="1151" r="150" fill="none" stroke="var(--dark)" stroke-width="3"/>
    </svg>
    <div class="fold fold--a"></div>
    <div class="fold fold--b"></div>

    <section class="intro-card">
      <svg width="392" height="939" viewBox="0 0 392 939">
        <circle cx="300" cy="-40" r="222" fill="#b08660" role="img" aria-label="Foto: Besen und Kehrschaufel auf Holzboden"/>
        <circle cx="300" cy="-40" r="238" fill="none" stroke="var(--red)" stroke-width="3"/>
        <circle cx="404" cy="347" r="48" fill="none" stroke="var(--red)" stroke-width="3"/>
        <circle cx="40" cy="942" r="55" fill="none" stroke="#fff" stroke-width="3"/>
      </svg>
      <div class="intro-text">
        <p>Sie benötigen Unterstützung im Haushalt? Wir sind für Sie da!</p>
        <p>Unsere Dienst&shy;leistungen um&shy;fassen <strong>Haushalts&shy;hilfen und Begleiter für den Alltag</strong>.</p>
        <p>Wir sind Spezialisten für die Be&shy;ratung von pflege&shy;bedürftigen Menschen, die Anspruch auf eine Haushalts&shy;hilfe von ihrer Pflege&shy;kasse haben.</p>
        <p>Zusätzlich sind Familien und Single&shy;haushalte, die Hilfe im Haushalt benötigen, ebenfalls herzlich willkommen.</p>
      </div>
      <div class="audience audience--care">
        <svg width="60" height="74" viewBox="0 0 60 74" fill="none" stroke="#fff" stroke-width="2">
          <circle cx="30" cy="24" r="15"/><path d="M18 14q12-12 24 0"/><path d="M8 72q0-24 22-24t22 24"/>
        </svg>pflegebedürftige Menschen</div>
      <div class="audience audience--family">
        <svg width="80" height="74" viewBox="0 0 80 74" fill="none" stroke="#fff" stroke-width="2">
          <circle cx="28" cy="30" r="13"/><circle cx="52" cy="22" r="14"/><path d="M6 72q0-22 22-22t22 22"/><path d="M40 46q6-6 12-6 22 0 22 26"/>
        </svg>Familien &amp; Single-haushalte</div>
    </section>

    <h2 class="heading heading--why"><span class="light">WARUM</span><span class="bold">WOLKENMUT?</span></h2>
    <p class="body body--why">Um sie zu entlasten, bietet <span class="brand">Wolkenmut</span> bedarfs&shy;orientierte Hilfe rund um den Haushalt an. Neben unserem breiten Spektrum an Services gibt es noch weitere Vorteile, warum Sie uns als starken Dienst&shy;leistungs&shy;partner vertrauen können.</p>

    <div class="benefits-frame"></div>
    <div class="benefit b1">Abrechnung mit allen Pflege-kassen möglich</div>
    <div class="benefit b2">Auch über die Verhinderungs-pflege</div>
    <div class="benefit b3">Hilfe bei der Antragsstellung</div>
    <div class="benefit b4">Abrechnung über den Entlastungsbetrag von<br>min. 125 € mtl. ab Pflegegrad 1 möglich</div>

    <h2 class="heading heading--services"><span class="light">UNSERE</span><span class="bold">LEISTUNGEN.</span></h2>
    <p class="body body--services">Zu unseren vielfältigen Leistungen im Bereich Haushalts&shy;hilfen und Alltags&shy;begleiter zählen unter anderem:</p>

    <div class="service" style="left:529px">
      <svg width="90" height="88" viewBox="0 0 90 88" fill="none" stroke="var(--red)" stroke-width="2.5">
        <path d="M22 82V40a24 24 0 0 1 48 0v8"/><rect x="52" y="42" width="34" height="40" rx="12"/><circle cx="72" cy="70" r="10"/><path d="M6 82h26l-6-8H12z"/>
      </svg>Haushalts-<br>hilfe</div>
    <div class="service" style="left:689px">
      <svg width="70" height="88" viewBox="0 0 70 88" fill="none" stroke="var(--red)" stroke-width="2.5">
        <rect x="6" y="16" width="50" height="68"/><path d="M56 16l8 6v62h-8"/><path d="M14 16l4-12 8 8 8-10 8 10 8-6 4 10"/>
      </svg>Einkaus-<br>service</div>
    <div class="service" style="left:846px">
      <svg width="70" height="88" viewBox="0 0 70 88" fill="none" stroke="var(--red)" stroke-width="2.5">
        <rect x="4" y="2" width="62" height="84"/><path d="M4 16h62M4 76h62"/><circle cx="35" cy="46" r="20"/><circle cx="35" cy="46" r="12"/><circle cx="14" cy="9" r="2"/><rect x="40" y="6" width="18" height="6"/>
      </svg>Wäsche-<br>service</div>
    <div class="service" style="left:1004px">
      <svg width="96" height="88" viewBox="0 0 96 88" fill="none" stroke="var(--red)" stroke-width="2.5">
        <path d="M80 2l-10 50"/><path d="M58 50h24l4 32H52z"/><path d="M62 58v24M70 58v24M78 58v24"/><circle cx="16" cy="74" r="6"/><circle cx="32" cy="70" r="7"/><circle cx="10" cy="60" r="3"/><circle cx="28" cy="56" r="3"/><circle cx="44" cy="62" r="4"/>
      </svg>Kehrwoche</div>
    <div class="service" style="left:1162px">
      <svg width="90" height="88" viewBox="0 0 90 88" fill="none" stroke="var(--red)" stroke-width="2.5">
        <path d="M52 4l30 30M60 30l-34 34M40 76l24-24 20 20-8 8-16-16"/><path d="M34 26l3 7 7 3-7 3-3 7-3-7-7-3 7-3z"/><path d="M12 10l2 5 5 2-5 2-2 5-2-5-5-2 5-2z"/><path d="M10 46l12 12"/>
      </svg>Fenster-<br>reinigung</div>
    <div class="service" style="left:1321px">
      <svg width="90" height="88" viewBox="0 0 90 88" fill="none" stroke="var(--red)" stroke-width="2.5">
        <path d="M45 84C14 62 6 48 6 36a18 18 0 0 1 39-10 18 18 0 0 1 39 10c0 12-8 26-39 48z"/><path d="M38 60V42a8 8 0 0 1 16 0"/><path d="M45 2v8M24 8l5 6M66 8l-5 6"/>
      </svg>Alltags-<br>begleitung</div>

    <div class="photo" role="img" aria-label="Foto: Hand im blauen Handschuh mit Sprühflasche beim Reinigen"></div>
  </div>
</div>
</body>
</html>
```